kolvarin.link kolvarin.space kolvarin.press website

The website is named KOLVARIN and it will have 3 domain names. kolvarin.link, press, space.
I'd like it to be viewed on Pads, pcs and phones.

page menu:

kolvarin.link(start page): presentation of company. (creative, design, app, new product innovation.)
Here we'll need sosial media icons: plimber, vendoloop, mirtavel, trelvanet. (light but some 'fruity' colors)

kolvarin.press: blog. It will be a 75% picture blog > rest will be text. I need to be able to resize pictures and shape columns to picture size. (light but some 'fruity' colors)

kolvarin.space : the fun part of this web design, however, on entering the page I'd like a non-disclosure agreement where viewer simply click "yes, I agree" after filling out contact info. (check attached document)
We will have space here for uploading PDF files viewers can download. There is also a blog space here to tell in brief about the PDF file. (maybe a space/sci-fi theme her e.g spacechimp, Laika the space dog?)

I will attach the logo here I want you to use > and develop for the .space .press webpage. The logo i uploaded is for the .link page.

Target Market(s)

venture capitalists

Number of Pages Required

3 page

Requirements
Must have
• a few 'fruity colors' but mostly white and grey

```html
<!DOCTYPE html>
<html lang="en">
<head>
<meta charset="utf-8">
<title>KOLVARIN — Creative Design and App Creation</title>
<link rel="stylesheet" href="https://fonts.googleapis.com/css2?family=Audiowide&family=Open+Sans:wght@400;600;700&family=Oswald:wght@400;500&display=swap">
<style>
  :root{
    --red:#e8504c;
    --red-deep:#d8322c;
    --green:#7cb342;
    --green-dark:#5e9a2c;
    --orange:#f29a1f;
    --yellow:#f4c21d;
    --blue:#1f7fc4;
    --ink:#333;
    --paper:#f3f3f3;
    --white:#fff;
    --plum-1:#5f4256;
    --plum-2:#8a5c63;
    --menu-dark:#3a3a3a;
  }
  *{box-sizing:border-box;margin:0;padding:0}
  html,body{width:1200px;height:3333px;overflow:hidden}
  body{position:relative;background:var(--white);font-family:"Open Sans",Arial,sans-serif;color:var(--ink)}
  .abs{position:absolute}
  .display{font-family:"Audiowide","Arial Black",sans-serif;letter-spacing:2px;white-space:nowrap}

  /* hero */
  .hero{left:0;top:0;width:1200px;height:573px;background:linear-gradient(135deg,#727272,#5c5c5c 60%,#676767)}
  .hero-devices{left:700px;top:64px;width:466px;height:460px;border-radius:16px;
    background:linear-gradient(160deg,#262626 0,#3b3b3b 45%,#5a6a7a 62%,#d5d5d5 63%,#f0f0f0 100%);
    box-shadow:0 18px 30px rgba(0,0,0,.25)}
  .brand{left:235px;top:110px;width:240px;font-size:40px;color:var(--white);text-align:center;line-height:1}
  .brand-dot{display:block;width:34px;height:34px;border-radius:50%;background:var(--yellow);margin:16px auto 0}
  .hero-title{left:78px;top:284px;font-size:25px;color:var(--white)}
  .hero-sub{left:78px;top:320px;font-size:17px;color:var(--white);letter-spacing:1.2px}
  .avail{font-family:"Oswald",sans-serif;font-size:12px;letter-spacing:1px;text-transform:uppercase}
  .hero-avail{left:171px;top:375px;width:353px;text-align:center;color:var(--white)}
  .store{display:flex;align-items:center;gap:10px;padding-left:14px;height:49px;color:var(--white);font-family:"Oswald",sans-serif;line-height:1.05;text-decoration:none}
  .store b{font-weight:500;font-size:13px;text-transform:uppercase;display:block}
  .store small{font-size:9px;text-transform:uppercase;opacity:.85}
  .store i{width:22px;height:22px;border-radius:50%;background:var(--white);opacity:.9;flex:none}
  .store-grey{background:#9a9a9a}
  .store-green{background:var(--green)}

  /* nav */
  .nav{left:0;top:573px;width:1200px;height:56px;background:var(--red)}
  .nav a,.nav span{position:absolute;top:20px;color:var(--white);text-decoration:none;font-family:"Oswald",sans-serif;font-size:13px;letter-spacing:.5px;text-transform:uppercase}

  /* intro */
  .intro{left:0;top:629px;width:1200px;height:515px;background:var(--paper)}
  .intro-art{left:78px;top:78px;width:520px;height:437px;border-radius:10px 10px 0 0;background:linear-gradient(120deg,#7a5a34,#e2b73a 40%,#f0ece4 65%,#9dc7b4)}
  .intro-title{left:638px;top:102px;font-size:24px;line-height:33px;color:var(--red-deep);letter-spacing:1.5px}
  .intro-lead{left:644px;top:207px;width:500px;font-size:16px;line-height:24px}
  .intro-body{left:644px;top:300px;width:500px;font-size:13px;line-height:21px;color:#777}
  .btn-more{left:649px;top:386px;width:169px;height:47px;border-radius:24px;background:var(--green);color:var(--white);font-family:"Oswald",sans-serif;font-size:13px;display:flex;align-items:center;padding-left:52px;text-decoration:none}
  .btn-more i{position:absolute;right:6px;top:7px;width:33px;height:33px;border-radius:50%;background:var(--green-dark)}

  /* features */
  .features{left:0;top:1144px;width:1200px;height:812px;background:linear-gradient(180deg,var(--plum-1),#77525e 55%,var(--plum-2))}
  .section-title{width:1200px;text-align:center;font-size:31px}
  .section-sub{width:1200px;text-align:center;font-size:14px}
  .feat-title{font-size:14px;font-weight:700;color:var(--white)}
  .feat-text{font-size:12px;line-height:18px;color:#e3d4d8;margin-top:14px}
  .feat-left{left:70px;width:246px;text-align:right}
  .feat-right{left:871px;width:250px}
  .phone{left:484px;top:216px;width:232px;height:475px}

  /* screenshots */
  .shots{left:0;top:1956px;width:1200px;height:655px;background:var(--white)}
  .shot{top:195px;height:353px;border:1px solid #ddd;background:#f4f4f4;overflow:hidden;font-size:7px;color:#555}
  .shot-status{height:12px;background:#4d8e2a;color:#fff;font-size:6px;padding:2px 6px;display:flex;justify-content:space-between}
  .shot-bar{height:26px;background:var(--green);color:#fff;font-size:10px;font-weight:600;text-align:center;line-height:26px}
  .shot-tabs{height:20px;background:#fff;display:flex;gap:10px;padding:0 6px;align-items:center;font-size:7px;border-bottom:1px solid #ddd;white-space:nowrap}
  .shot-tabs b{border-bottom:2px solid var(--green);padding-bottom:3px}
  .tile-grid{display:grid;grid-template-columns:1fr 1fr;gap:3px;padding:3px}
  .tile{height:93px}
  .t1{background:linear-gradient(135deg,#c9a27a,#6b4a3a)}
  .t2{background:linear-gradient(135deg,#4a4a4a,#a3834f)}
  .t3{background:linear-gradient(135deg,#2d5f8a,#4a9cc5)}
  .t4{background:linear-gradient(135deg,#3b6d8f,#e0524e)}
  .t5{background:linear-gradient(135deg,#2e4d78,#7a8fb0)}
  .t6{background:linear-gradient(135deg,#1e2c3a,#4b6f8f)}
  .profile-top{background:#fff;height:142px;text-align:center;padding-top:14px}
  .avatar{width:56px;height:56px;border-radius:50%;margin:0 auto 8px;background:linear-gradient(135deg,#e9b27e,#9c6a45);border:3px solid var(--green)}
  .profile-name{font-size:9px;font-weight:600;color:#333}
  .profile-url{font-size:6px;color:#999;margin-top:2px}
  .stat-row{display:flex;justify-content:space-around;font-size:7px;color:#666;padding:8px 6px;background:#fff;border-top:1px solid #eee}
  .shot-head{display:flex;gap:6px;align-items:center;padding:8px;background:#fff}
  .shot-head i{width:22px;height:22px;border-radius:50%;background:linear-gradient(135deg,#e9b27e,#9c6a45);flex:none}
  .shot-head b{font-size:9px;color:#333;display:block}
  .shot-head small{font-size:6px;color:var(--green)}
  .shot-image{height:148px;background:linear-gradient(180deg,#8fc4d8,#5f9db8)}
  .comment{display:flex;gap:6px;align-items:center;padding:8px;background:#fff;border-top:1px solid #eee;margin-top:6px}
  .comment i{width:20px;height:20px;border-radius:50%;background:linear-gradient(135deg,#c79b72,#7a5a44);flex:none}
  .comment b{font-size:7px;color:var(--green);display:block}
  .menu-shot{background:var(--menu-dark);color:#ddd}
  .menu-shot .shot-status{background:#222}
  .menu-head{height:30px;background:#2b2b2b}
  .menu-item{height:27px;line-height:27px;padding-left:24px;font-size:8px;border-bottom:1px solid #444;position:relative}
  .menu-item::before{content:"";position:absolute;left:8px;top:10px;width:7px;height:7px;border-radius:2px;background:#888}
  .menu-item.active{background:var(--green);color:#fff}
  .menu-item.active::before{background:#fff}
  .dot{top:602px;width:11px;height:11px;border-radius:50%;border:1px solid #aaa}

  /* newsletter */
  .news{left:0;top:2611px;width:1200px;height:393px;background:linear-gradient(180deg,#e66a22,#f08a2f 55%,#c9481b)}
  .news-text{left:0;top:174px;width:1200px;text-align:center;color:#fde7d4;font-size:13px;line-height:19px}
  .news-input{left:344px;top:242px;width:363px;height:36px;border-radius:18px;background:var(--white);font-size:11px;color:#999;padding:10px 22px}
  .news-btn{left:716px;top:242px;width:131px;height:36px;border-radius:18px;background:var(--green);color:var(--white);font-family:"Oswald",sans-serif;font-size:12px;text-align:center;line-height:36px}

  /* footer */
  .footer{left:0;top:3004px;width:1200px;height:329px;background:var(--paper)}
  .mail-tab{left:555px;top:-45px;width:90px;height:90px;border-radius:50%;background:#cfcfcf}
  .social{width:62px;height:62px;border-radius:50%;color:var(--white);font-size:9px;font-weight:700;display:flex;align-items:center;justify-content:center;top:209px;text-decoration:none}
</style>
</head>
<body>

<header class="abs hero">
  <div class="abs hero-devices" role="img" aria-label="Laptop and tablet showing the app feature screens, set on a table with citrus fruit"></div>
  <div class="abs brand display">KOLVARIN<span class="brand-dot"></span></div>
  <h1 class="abs hero-title display">WE PROVIDE CREATIVE DESIGN</h1>
  <p class="abs hero-sub display">AND APP CREATION, NEW PRODUCT INNOVATION ETC</p>
  <p class="abs hero-avail avail">Available on</p>
  <a class="abs store store-grey" style="left:171px;top:404px;width:167px"><i></i><span><b>Download app</b><small>from Appvale</small></span></a>
  <a class="abs store store-green" style="left:356px;top:404px;width:168px"><i></i><span><b>Download app</b><small>from Playmeadow</small></span></a>
</header>

<nav class="abs nav">
  <a style="left:167px">Home</a><span style="left:250px">/</span>
  <a style="left:305px">About us</a><span style="left:410px">/</span>
  <a style="left:466px">Products</a><span style="left:580px">/</span>
  <a style="left:635px">App features</a><span style="left:766px">/</span>
  <a style="left:812px">Blog</a><span style="left:900px">/</span>
  <a style="left:955px">Contact us</a>
</nav>

<section class="abs intro">
  <div class="abs intro-art" role="img" aria-label="Three phones showing illustrated characters and a pineapple"></div>
  <h2 class="abs intro-title display">APP CREATION AND NEW PRODUCT<br>INNOVATION ETC</h2>
  <p class="abs intro-lead">Lorem ipsum dolor sit amet, consectetur adipiscing elit. Pellentesque vitae arcu sit amet urna sagittis consectetur in a ante. Suspendisse potenti.</p>
  <p class="abs intro-body">Cum sociis natoque penatibus et magnis dis parturient montes, nascetur ridiculus mus. Duis semper erat quis nisi blandit, ut suscipit sem porta.</p>
  <a class="abs btn-more">READ MORE<i></i>
    <svg class="abs" style="right:15px;top:17px" width="14" height="14" viewBox="0 0 14 14"><path d="M2 7h10M8 3l4 4-4 4" stroke="#fff" stroke-width="2" fill="none"/></svg>
  </a>
</section>

<section class="abs features" role="region" aria-label="Features on a dusky desert background">
  <h2 class="abs section-title display" style="top:72px;color:var(--white)">BRILLIANT FEATURES</h2>
  <p class="abs section-sub" style="top:124px;color:#e3d4d8">Revolutionary Mobile Marketing Software Platform Features</p>

  <div class="abs feat-left" style="top:235px"><p class="feat-title">Mobile Text Message Marketing</p><p class="feat-text">Text message marketing forms the core<br>of every campaign we run.</p></div>
  <div class="abs feat-left" style="top:409px"><p class="feat-title">Bulk SMS Service</p><p class="feat-text">Teams and organisations use bulk<br>messaging to reach people fast.</p></div>
  <div class="abs feat-left" style="top:580px"><p class="feat-title">Mobile Keyword Technology</p><p class="feat-text">Set up as many keywords as you'd like<br>in minutes, then track replies.</p></div>

  <div class="abs feat-right" style="top:235px"><p class="feat-title">Lorem ipsum dolor sit amet</p><p class="feat-text">Our mobile text messaging reminder<br>feature allows you to easily queue and send</p></div>
  <div class="abs feat-right" style="top:409px"><p class="feat-title">Mobile Coupons</p><p class="feat-text">You can offer free gifts, discounts,<br>incentives, and reminders to your</p></div>
  <div class="abs feat-right" style="top:580px"><p class="feat-title">Pellentesque vitae arcu sit amet</p><p class="feat-text">You can offer free gifts, discounts,<br>incentives, and reminders to your</p></div>

  <svg class="abs" style="left:0;top:0" width="1200" height="812" viewBox="0 0 1200 812">
    <g stroke="#3a2a30" stroke-width="3">
      <circle cx="400" cy="278" r="51" fill="#fff"/><circle cx="400" cy="278" r="43" fill="#d8322c"/>
      <circle cx="400" cy="452" r="51" fill="#fff"/><circle cx="400" cy="452" r="43" fill="#f29a1f"/>
      <circle cx="400" cy="623" r="51" fill="#fff"/><circle cx="400" cy="623" r="43" fill="#8e2a2a"/>
      <circle cx="793" cy="278" r="51" fill="#fff"/><circle cx="793" cy="278" r="43" fill="#e8e4de"/>
      <circle cx="793" cy="452" r="51" fill="#fff"/><circle cx="793" cy="452" r="43" fill="#7cb342"/>
      <circle cx="793" cy="623" r="51" fill="#fff"/><circle cx="793" cy="623" r="43" fill="#f4c21d"/>
    </g>
    <g fill="#fff" stroke="#3a2a30" stroke-width="2">
      <path d="M378 266h44v24h-26l-10 9v-9h-8z"/>
      <path d="M388 466h24l-4-6v-14a8 8 0 0 0-16 0v14z"/><circle cx="400" cy="470" r="4"/>
      <path d="M387 603h20l8 8v34h-28z"/>
      <circle cx="793" cy="278" r="20"/><path d="M793 266v12h9" fill="none"/>
      <circle cx="793" cy="452" r="18" fill="#3a2a30"/><path d="M785 460l16-16" stroke="#fff"/>
      <circle cx="793" cy="623" r="18" fill="#3a2a30"/><circle cx="793" cy="623" r="7"/>
    </g>
  </svg>

  <svg class="abs phone" width="232" height="475" viewBox="0 0 232 475">
    <defs><linearGradient id="screen" x1="0" y1="0" x2="0" y2="1"><stop offset="0" stop-color="#e07f86"/><stop offset="1" stop-color="#f2c2a0"/></linearGradient></defs>
    <rect x="1" y="1" width="230" height="473" rx="34" fill="#fafafa" stroke="#cfcfcf" stroke-width="2"/>
    <rect x="14" y="64" width="204" height="348" fill="url(#screen)" role="img" aria-label="App start screen over desert dunes"/>
    <text x="116" y="200" text-anchor="middle" font-family="Audiowide, sans-serif" font-size="24" fill="#3a2a30">KOLVARIN</text>
    <rect x="90" y="30" width="52" height="6" rx="3" fill="#bbb"/>
    <circle cx="116" cy="442" r="18" fill="none" stroke="#bbb" stroke-width="2"/>
  </svg>
</section>

<section class="abs shots">
  <h2 class="abs section-title display" style="top:64px;color:var(--red-deep)">SCREENSHOTS</h2>
  <p class="abs section-sub" style="top:124px;color:#888">Showcase your app screenshots into a nice carousel below. You can add as many screenshots as you want.</p>

  <div class="abs shot" style="left:84px;width:189px">
    <div class="shot-status"><span>●●●●● CELL</span><span>4:21 PM</span><span>22%</span></div>
    <div class="shot-bar">Shots</div>
    <div class="shot-tabs"><b>Following</b><span>Suggestions</span><span>Popular</span><span>Everyone</span></div>
    <div class="tile-grid" role="img" aria-label="Grid of shot thumbnails">
      <div class="tile t1"></div><div class="tile t2"></div>
      <div class="tile t3"></div><div class="tile t4"></div>
      <div class="tile t5"></div><div class="tile t6"></div>
    </div>
  </div>

  <div class="abs shot" style="left:360px;width:191px">
    <div class="shot-status"><span>●●●●● CELL</span><span>4:21 PM</span><span>22%</span></div>
    <div class="shot-bar">Profile</div>
    <div class="profile-top">
      <div class="avatar" role="img" aria-label="Profile photo"></div>
      <p class="profile-name">Tomas Relik</p>
      <p class="profile-url">www.tomasrelik.com</p>
    </div>
    <div class="stat-row"><span>▣ 26</span><span>◫ 3</span><span>♡ 236</span><span>◌ 12</span></div>
    <div class="tile-grid" role="img" aria-label="Grid of shot thumbnails">
      <div class="tile t2"></div><div class="tile t1"></div>
      <div class="tile t4"></div><div class="tile t3"></div>
    </div>
  </div>

  <div class="abs shot" style="left:638px;width:198px">
    <div class="shot-status"><span>●●●●● CELL</span><span>4:21 PM</span><span>22%</span></div>
    <div class="shot-bar">Shot</div>
    <div class="shot-head"><i></i><span><b>Flat Icons</b><small>by Tomas Relik</small></span></div>
    <div class="shot-image" role="img" aria-label="Shot preview of a flat icon set"></div>
    <div class="stat-row"><span style="color:var(--green)">♥ 287</span><span>◌ 13</span><span>◎ 140</span></div>
    <div class="comment"><i></i><span><b>Jon Pellar</b>Awesome icon set!</span></div>
  </div>

  <div class="abs shot menu-shot" style="left:916px;width:195px">
    <div class="shot-status"><span>●●●●● CELL</span><span>4:21 PM</span><span>22%</span></div>
    <div class="menu-head"></div>
    <div class="menu-item">Profile</div>
    <div class="menu-item">Notifications</div>
    <div class="menu-item">Upload Shot</div>
    <div class="menu-item active">Shots</div>
    <div class="menu-item">Explore</div>
    <div class="menu-item">Designers</div>
    <div class="menu-item">Teams</div>
    <div class="menu-item">Jobs</div>
    <div class="menu-item">Sign Out</div>
  </div>

  <span class="abs dot" style="left:535px"></span>
  <span class="abs dot" style="left:564px"></span>
  <span class="abs dot" style="left:595px;background:#aaa"></span>
  <span class="abs dot" style="left:624px"></span>
  <span class="abs dot" style="left:653px"></span>
</section>

<section class="abs news" role="region" aria-label="Orange planet landscape with a rocket and a cratered moon">
  <h2 class="abs section-title display" style="top:112px;color:var(--white)">KNOW THE LATEST NEWS OF KOLVARIN</h2>
  <p class="abs news-text">Donec vulputate, urna ut volutpat pretium, quam diam varius nunc, sed<br>fermentum tortor urna sed nulla nulla vel magna viverra</p>
  <div class="abs news-input">Enter Your Email Address</div>
  <div class="abs news-btn">SUBSCRIBE</div>
</section>

<footer class="abs footer">
  <div class="abs mail-tab"></div>
  <svg class="abs" style="left:585px;top:2px" width="30" height="22" viewBox="0 0 30 22"><rect x="1" y="1" width="28" height="20" fill="none" stroke="#fff" stroke-width="2"/><path d="M1 1l14 11L29 1" fill="none" stroke="#fff" stroke-width="2"/></svg>
  <p class="abs avail" style="left:0;top:82px;width:1200px;text-align:center;color:#777">Available on</p>
  <a class="abs store store-grey" style="left:400px;top:123px;width:191px;height:51px"><i></i><span><b>Download app</b><small>from Appvale</small></span></a>
  <a class="abs store store-green" style="left:611px;top:123px;width:191px;height:51px"><i></i><span><b>Download app</b><small>from Playmeadow</small></span></a>
  <a class="abs social" style="left:451px;background:var(--red-deep)">mirtavel</a>
  <a class="abs social" style="left:529px;background:var(--orange)">plimber</a>
  <a class="abs social" style="left:607px;background:var(--blue)">vendoloop</a>
  <a class="abs social" style="left:682px;background:var(--yellow)">trelvanet</a>
</footer>

</body>
</html>
```